wealth management firm, professional group, new model

we have a logo that works but we need a card, white background using our colors...clean look

our tag line if can be used in

Guiding Clients Toward Ownership

```html
<!DOCTYPE html>
<html lang="en">
<head>
<meta charset="utf-8">
<title>Arden Wealth Partners — Business Card</title>
<link rel="stylesheet" href="https://fonts.googleapis.com/css2?family=Montserrat:ital,wght@0,400;0,500;1,400&display=swap">
<style>
  :root {
    --navy: #14244a;
    --card: #f1f1f1;
    --backdrop: #262626;
  }
  * { margin: 0; padding: 0; box-sizing: border-box; }
  html, body {
    width: 1200px; height: 576px; overflow: hidden;
    background: var(--backdrop);
    font-family: "Montserrat", sans-serif;
    color: var(--navy);
  }
  .card {
    position: absolute;
    background: var(--card);
    border-radius: 10px;
    overflow: hidden;
  }
  .card--front { left: 102px; top: 139px; width: 484px; height: 292px; }
  .card--back  { left: 596px; top: 138px; width: 480px; height: 291px; }

  .front-wordmark {
    position: absolute; left: 0; right: 0; top: 134px;
    text-align: center;
  }
  .front-wordmark .brand-name {
    font-size: 38px; font-weight: 400; letter-spacing: 0.42em;
    margin-right: -0.42em; line-height: 1;
  }
  .front-wordmark .brand-sub {
    margin-top: 22px;
    font-size: 15px; font-weight: 400; letter-spacing: 0.14em;
    margin-right: -0.14em;
  }

  .holder { position: absolute; left: 22px; top: 44px; }
  .holder-name { font-size: 21px; font-weight: 500; line-height: 1.1; }
  .holder-title { font-size: 13px; font-weight: 500; margin-top: 3px; }

  .back-wordmark { position: absolute; right: 30px; top: 42px; text-align: right; }
  .back-wordmark .brand-name {
    font-size: 28px; font-weight: 400; letter-spacing: 0.45em;
    margin-right: -0.45em; line-height: 1;
  }
  .back-wordmark .brand-sub {
    margin-top: 10px;
    font-size: 10.5px; font-weight: 400; letter-spacing: 0.3em;
    margin-right: -0.3em;
  }

  .contact-list { position: absolute; left: 28px; top: 178px; list-style: none; }
  .contact-list li {
    display: flex; align-items: center; height: 20px;
    font-size: 12.5px; font-weight: 400;
  }
  .contact-list svg { width: 11px; height: 11px; margin-right: 8px; fill: var(--navy); }

  .divider {
    position: absolute; left: 0; right: 0; top: 245px;
    height: 3px; background: var(--navy);
  }
  .tagline {
    position: absolute; left: 22px; top: 259px;
    font-size: 12.5px; font-style: italic; letter-spacing: 0.04em;
  }
</style>
</head>
<body>
  <section class="card card--front">
    <div class="front-wordmark">
      <div class="brand-name">ARDEN</div>
      <div class="brand-sub">WEALTH PARTNERS</div>
    </div>
  </section>

  <section class="card card--back">
    <div class="holder">
      <div class="holder-name">Daniel Arden</div>
      <div class="holder-title">Managing Director</div>
    </div>

    <div class="back-wordmark">
      <div class="brand-name">ARDEN</div>
      <div class="brand-sub">WEALTH PARTNERS</div>
    </div>

    <ul class="contact-list">
      <li>
        <svg viewBox="0 0 12 12" aria-hidden="true"><path d="M1 4.2C1 2.6 3 1.6 6 1.6s5 1 5 2.6v.8H8.6V3.9C8 3.5 7 3.3 6 3.3s-2 .2-2.6.6V5H1z"/><path d="M3.4 5.6h5.2l2 4.8H1.4z"/></svg>
        555-014-2270
      </li>
      <li>
        <svg viewBox="0 0 12 12" aria-hidden="true"><path d="M0.8 2.5h10.4v7H0.8z"/><path d="M1.2 3l4.8 3.6L10.8 3" fill="none" stroke="#f1f1f1" stroke-width="1"/></svg>
        daniel@ardenwealth.com
      </li>
      <li>
        <svg viewBox="0 0 12 12" aria-hidden="true"><circle cx="6" cy="6" r="5"/><path d="M1 6h10M6 1v10M6 1c-2.4 2.8-2.4 7.2 0 10M6 1c2.4 2.8 2.4 7.2 0 10" fill="none" stroke="#f1f1f1" stroke-width="0.8"/></svg>
        www.ardenwealth.com
      </li>
    </ul>

    <div class="divider"></div>
    <p class="tagline">Guiding Clients Toward Ownership</p>
  </section>
</body>
</html>
```